Request for Web Design Services – Lantern Trail

We are excited to announce a new project and are seeking talented web designers to create a visually stunning and intuitive website for our upcoming service, "Lantern Trail." This platform is dedicated to assisting foreign visitors in planning their journeys across Japan by highlighting the nation's beautiful shrines and temples. Please refer to the attached document for detailed design requirements.

Project Overview:
-Site Name: Lantern Trail
-Target Audience: Visitors to Japan
-Usage Scenario: Trip planning before and during the visit to Japan

Functionalities:
-Plotting the names and locations of shrines and temples across Japan
-Enabling users to select multiple shrines and temples and proposing optimal touring routes
-Intuitive user interface without relying heavily on language explanations

Deliverables:
-Source code (HTML, CSS, JavaScript, etc.)
-Site name logo
-Icons
-Favicon

Deadline:May 1, 2024

Design Requirements:
-Responsive design for both PC and mobile devices

Design Preferences:
-Catchy design suitable for coverage in domestic and international news media
-Unique design not typically created by Japanese designers
-Incorporation of Japanese traditions while maintaining a modern aesthetic
-Inclusion of motifs representing shrines and temples, such as bells and omikuji

We look forward to receiving your creative proposals and collaborating on this exciting project.

Best regards

Target Market(s)

Visitors to Japan

Industry/Entity Type

Information Technology

Coding

Coded - Design and coding required

Number of Pages Required

3 page

```html
<!DOCTYPE html>
<html lang="en">
<head>
<meta charset="utf-8">
<title>Lantern Trail – Map</title>
<link rel="stylesheet" href="https://fonts.googleapis.com/css2?family=Nunito:wght@400;500;600;700&display=swap">
<style>
  :root{
    --blue:#0a7fd6;
    --green:#25a244;
    --ink:#1c1c1c;
    --white:#ffffff;
    --track:#d6d6d6;
    --map-green:#cfe3c8;
    --map-grey:#ecebe6;
    --map-water:#aad3ef;
  }
  *{box-sizing:border-box;margin:0;padding:0}
  html,body{width:1200px;height:720px;overflow:hidden}
  body{position:relative;font-family:"Nunito",sans-serif;color:var(--ink);background:var(--white)}
  .site-header{position:absolute;left:0;top:0;width:1200px;height:72px;background:var(--white);z-index:5}
  .menu-icon{position:absolute;left:24px;top:26px;width:27px;height:20px}
  .menu-icon span{display:block;height:3px;background:var(--ink);border-radius:2px;margin-bottom:5.5px}
  .site-title{position:absolute;left:72px;top:20px;font-size:22px;font-weight:500;letter-spacing:.5px}
  .view-toggle{position:absolute;left:960px;top:19px;width:69px;height:35px;border-radius:18px;background:var(--green)}
  .view-toggle svg{position:absolute;left:12px;top:9px}
  .view-toggle .knob{position:absolute;right:9px;top:9px;width:17px;height:17px;border-radius:50%;background:var(--white)}
  .search-btn{position:absolute;left:1047px;top:21px;width:128px;height:34px;border-radius:17px;background:var(--blue);color:var(--white);font-size:13px;font-weight:500;display:flex;align-items:center;justify-content:center;gap:6px}
  .map{position:absolute;left:0;top:72px;width:1200px;height:648px;
    background:
      radial-gradient(ellipse 180px 120px at 700px 470px,var(--map-water),transparent 70%),
      radial-gradient(ellipse 260px 200px at 160px 380px,var(--map-green),transparent 75%),
      radial-gradient(ellipse 300px 220px at 1020px 200px,var(--map-green),transparent 75%),
      linear-gradient(160deg,#e4ecdf 0%,var(--map-grey) 45%,#e6eee1 100%)}
  .planning-btn{position:absolute;left:50px;top:109px;width:128px;height:34px;border-radius:17px;background:var(--blue);color:var(--white);font-size:14px;font-weight:500;display:flex;align-items:center;justify-content:space-between;padding:0 16px 0 18px;z-index:3}
  .pin{position:absolute;border-radius:50%;display:flex;align-items:center;justify-content:center;border:2px solid var(--white);z-index:2}
  .pin-360{width:47px;height:47px;background:var(--green);color:var(--white);flex-direction:column;font-size:11px;font-weight:700;line-height:1}
  .pin-360 svg{margin-bottom:2px}
  .pin-bell{width:36px;height:36px;background:var(--blue)}
  .place-card{position:absolute;left:494px;top:292px;width:140px;height:148px;background:var(--white);border-radius:5px;padding:9px;z-index:4;box-shadow:0 2px 6px rgba(0,0,0,.15)}
  .place-card .photo{width:120px;height:83px;background:linear-gradient(180deg,#2d6fc4 0%,#b0451f 45%,#7a2a14 100%)}
  .place-card p{font-size:13px;font-weight:500;line-height:19px;margin-top:9px;padding-left:3px}
  .place-card::after{content:"";position:absolute;left:63px;bottom:-9px;border:9px solid transparent;border-bottom:0;border-top-color:var(--white)}
  .filter-bar{position:absolute;left:200px;top:602px;width:804px;height:72px;background:rgba(255,255,255,.9);border-radius:6px;z-index:4}
  .filter-label{position:absolute;left:21px;top:28px;font-size:12px;display:flex;align-items:center;gap:6px}
  .filter-divider{position:absolute;left:95px;top:0;width:1px;height:72px;background:#e2e2e2}
  .range-track{position:absolute;left:113px;top:48px;width:672px;height:4px;background:var(--track)}
  .range-fill{position:absolute;left:101px;top:0;width:215px;height:4px;background:var(--blue)}
  .range-flag{position:absolute;top:19px;width:16px;height:17px;background:var(--blue);color:var(--white);font-size:10px;text-align:center;line-height:17px}
  .range-flag::after{content:"";position:absolute;left:5px;bottom:-4px;border:3px solid transparent;border-bottom:0;border-top:4px solid var(--blue)}
  .zoom{position:absolute;left:1157px;top:648px;width:24px;height:48px;background:var(--white);border-radius:4px;box-shadow:0 1px 3px rgba(0,0,0,.2);z-index:3;font-size:15px;color:#666;text-align:center;line-height:24px}
  .scale{position:absolute;left:1178px;top:704px;font-size:8px;color:#333;z-index:3}
</style>
</head>
<body>
<svg width="0" height="0" style="position:absolute">
  <defs>
    <symbol id="icon-pano" viewBox="0 0 20 16"><path d="M1 3 Q10 0 19 3 V14 Q10 11 1 14 Z" fill="none" stroke="currentColor" stroke-width="2"/><path d="M3 12 L7 7 L10 10 L13 6 L17 12 Z" fill="currentColor"/><circle cx="6" cy="5" r="1.3" fill="currentColor"/></symbol>
    <symbol id="icon-bell" viewBox="0 0 20 20"><path d="M10 2 C6.5 2 5 5 5 8 V12 L3 15 H17 L15 12 V8 C15 5 13.5 2 10 2 Z" fill="currentColor"/><circle cx="10" cy="17" r="2" fill="currentColor"/></symbol>
  </defs>
</svg>

<header class="site-header">
  <div class="menu-icon"><span></span><span></span><span></span></div>
  <div class="site-title">Lantern Trail</div>
  <div class="view-toggle"><svg width="24" height="18" style="color:#fff"><use href="#icon-pano"/></svg><span class="knob"></span></div>
  <div class="search-btn"><svg width="13" height="13" viewBox="0 0 14 14"><circle cx="6" cy="6" r="4.5" fill="none" stroke="#fff" stroke-width="1.6"/><path d="M9.5 9.5 L13 13" stroke="#fff" stroke-width="1.6"/></svg>Search Area</div>
</header>

<main class="map" role="img" aria-label="Road map of the greater Tokyo region with cities, rails and the bay">
</main>

<div class="planning-btn">Planning<svg width="9" height="14" viewBox="0 0 9 14"><path d="M1 1 L7 7 L1 13" fill="none" stroke="#fff" stroke-width="1.6"/></svg></div>

<div class="pin pin-360" style="left:426px;top:131px"><svg width="20" height="16" style="color:#fff"><use href="#icon-pano"/></svg>360</div>
<div class="pin pin-360" style="left:275px;top:265px"><svg width="20" height="16" style="color:#fff"><use href="#icon-pano"/></svg>360</div>
<div class="pin pin-360" style="left:185px;top:494px"><svg width="20" height="16" style="color:#fff"><use href="#icon-pano"/></svg>360</div>
<div class="pin pin-360" style="left:807px;top:242px"><svg width="20" height="16" style="color:#fff"><use href="#icon-pano"/></svg>360</div>
<div class="pin pin-360" style="left:1094px;top:166px"><svg width="20" height="16" style="color:#fff"><use href="#icon-pano"/></svg>360</div>
<div class="pin pin-360" style="left:999px;top:382px"><svg width="20" height="16" style="color:#fff"><use href="#icon-pano"/></svg>360</div>
<div class="pin pin-360" style="left:572px;top:590px"><svg width="20" height="16" style="color:#fff"><use href="#icon-pano"/></svg>360</div>

<div class="pin pin-bell" style="left:684px;top:132px"><svg width="18" height="18" style="color:#fff"><use href="#icon-bell"/></svg></div>
<div class="pin pin-bell" style="left:438px;top:300px"><svg width="18" height="18" style="color:#fff"><use href="#icon-bell"/></svg></div>
<div class="pin pin-bell" style="left:960px;top:255px"><svg width="18" height="18" style="color:#fff"><use href="#icon-bell"/></svg></div>
<div class="pin pin-bell" style="left:356px;top:437px"><svg width="18" height="18" style="color:#fff"><use href="#icon-bell"/></svg></div>
<div class="pin pin-bell" style="left:650px;top:444px"><svg width="18" height="18" style="color:#fff"><use href="#icon-bell"/></svg></div>
<div class="pin pin-bell" style="left:543px;top:461px"><svg width="18" height="18" style="color:#fff"><use href="#icon-bell"/></svg></div>
<div class="pin pin-bell" style="left:376px;top:590px"><svg width="18" height="18" style="color:#fff"><use href="#icon-bell"/></svg></div>
<div class="pin pin-bell" style="left:885px;top:588px"><svg width="18" height="18" style="color:#fff"><use href="#icon-bell"/></svg></div>

<div class="place-card">
  <div class="photo" role="img" aria-label="Photo of a red temple pagoda under blue sky"></div>
  <p>Akebono-ji Temple, Tokyo</p>
</div>

<section class="filter-bar">
  <div class="filter-label">Popular<svg width="7" height="12" viewBox="0 0 7 12"><path d="M1 1 L6 6 L1 11" fill="none" stroke="#1c1c1c" stroke-width="1.3"/></svg></div>
  <div class="filter-divider"></div>
  <div class="range-flag" style="left:207px">1</div>
  <div class="range-flag" style="left:418px">3</div>
  <div class="range-track"><div class="range-fill"></div></div>
</section>

<div class="zoom">+<br>−</div>
<div class="scale">X37</div>
</body>
</html>
```